Create a Big Data Website that is professional but has a creative flare to it.

I am after a modern business design for a company in the Big Data space however it still needs to have a wow value and something stand out from other corporate websites.
My competitors websites are to give you and idea of content:
www.tarnvilla.com
www.pluvoria.com
www.meridu4.com.au
www.quornaby.com
I have uploaded my company Logo so you can use that to make sure it matches your theme.

Target Market(s)

Banks, Insurance Companies, Government, Gas and Energy Companies and Food Manufacturing.

Industry/Entity Type

Consulting

Coding

Number of Pages Required

5+ page

Colors

Designer to choose colors to be used in the design.

Requirements
Must have
• Images, Diagrams around Big Data. Usage of information or graphs from sources like Velsham are fine to use.
Nice to have
• Interactive design use mouse overs, change in text, highlighting information for clear focus.
Should not have
• Cluttered Pages of Informaiton

```html
<!DOCTYPE html>
<html lang="en">
<head>
<meta charset="utf-8">
<title>Caliber Insight</title>
<link href="https://fonts.googleapis.com/css2?family=Open+Sans:ital,wght@0,300;0,400;0,600;0,700;1,400&display=swap" rel="stylesheet">
<style>
:root{
  --blue:#0b8fd8;
  --blue-dark:#12386b;
  --sky:#4fb0e3;
  --ink:#333;
  --muted:#666;
  --light:#f6f6f6;
  --line:#dcdcdc;
  --white:#fff;
}
*{margin:0;padding:0;box-sizing:border-box}
html,body{width:1200px;height:2786px;overflow:hidden}
body{font-family:"Open Sans",Arial,sans-serif;color:var(--ink);background:var(--white);position:relative}
section,header,footer{position:absolute;left:0;width:1200px}

.site-header{top:0;height:106px;background:var(--white)}
.brand{position:absolute;left:100px;top:30px;display:flex;align-items:center;gap:14px}
.brand-mark{width:44px;height:44px;background:var(--blue)}
.brand-name{font-size:34px;font-weight:700;color:var(--blue-dark);letter-spacing:-0.5px}
.main-nav{position:absolute;right:100px;top:42px;display:flex;gap:40px;font-size:14px;color:var(--ink)}
.main-nav .active{color:var(--blue)}
.main-nav svg{margin-top:2px}

.hero{top:106px;height:566px}
.hero-photo{position:absolute;inset:0;background:linear-gradient(120deg,#2b3139 0%,#4b5660 40%,#2e3640 70%,#1f252c 100%)}
.hero-title{position:absolute;top:158px;width:100%;text-align:center;color:var(--white);font-size:68px;font-weight:700;text-shadow:0 2px 6px rgba(0,0,0,.4)}
.hero-sub{position:absolute;top:240px;width:100%;text-align:center;color:var(--white);font-size:30px;font-weight:400}
.hero-btn{position:absolute;left:509px;top:305px;width:182px;height:52px;background:var(--blue);color:var(--white);font-size:22px;display:flex;align-items:center;justify-content:center;gap:10px}
.hero-arrow{position:absolute;top:240px}

.welcome{top:672px;height:381px;text-align:center}
.section-title{font-size:35px;font-weight:300;text-transform:uppercase}
.welcome .section-title{color:var(--blue);margin-top:62px}
.welcome p{width:870px;margin:22px auto 0;font-size:13.5px;line-height:27px;color:var(--muted)}
.welcome p+p{margin-top:27px}

.services{top:1053px;height:560px;background:var(--light);text-align:center}
.services .section-title{margin-top:50px;color:var(--ink)}
.services .intro{width:870px;margin:20px auto 0;font-size:13.5px;line-height:27px;color:var(--muted)}
.service-list{position:absolute;top:210px;left:0;width:100%}
.service{position:absolute;width:210px;text-align:center}
.service h3{margin-top:14px;font-size:14.5px;font-weight:600;color:var(--ink)}
.service p{margin-top:10px;font-size:11.5px;line-height:20px;color:var(--ink);height:42px}
.read-more{display:inline-block;margin-top:10px;width:121px;height:37px;line-height:37px;background:var(--blue);color:var(--white);font-size:13px;font-weight:600}

.testimonials{top:1613px;height:488px;text-align:center;color:var(--white)}
.testimonial-bg{position:absolute;inset:0;background:linear-gradient(180deg,#5ab6e6 0%,#3fa3dc 50%,#58b3e4 100%)}
.testimonials .section-title{position:relative;margin-top:58px}
.quote{position:relative;width:822px;margin:28px auto 0;font-size:13.5px;font-style:italic;line-height:30px}
.quote-mark{position:absolute;font-size:70px;font-weight:700;opacity:.55;line-height:1}
.avatar{position:absolute;left:530px;top:264px;width:140px;height:140px;border-radius:50%;border:7px solid var(--white);background:linear-gradient(180deg,#e8eef3,#9fb0bf)}
.client-name{position:absolute;top:415px;width:100%;font-size:15px;text-transform:uppercase;letter-spacing:1px}

.partners{top:2101px;height:344px;text-align:center}
.partners .section-title{margin-top:66px;color:var(--ink)}
.partner{position:absolute;top:158px;width:155px;height:95px;border:1px solid var(--line);display:flex;align-items:center;justify-content:center;font-size:15px;font-weight:600;color:var(--blue-dark)}
.partner-arrow{position:absolute;top:190px}

.site-footer{top:2445px;height:341px;background:var(--blue);color:var(--white)}
.footer-head{position:absolute;top:44px;font-size:17px;font-weight:600;text-transform:uppercase}
.link-col{position:absolute;top:90px;list-style:none;font-size:14px;line-height:32px}
.contact{position:absolute;left:461px;top:88px;font-size:14.5px;line-height:33px}
.contact-row{display:flex;align-items:center;gap:12px}
.newsletter-note{position:absolute;left:773px;top:84px;font-size:13.5px}
.signup{position:absolute;left:777px;top:111px;display:flex;height:39px}
.signup .field{width:219px;background:var(--white);color:#999;font-size:13px;padding:11px 14px;text-transform:uppercase}
.signup .submit{width:105px;background:var(--blue-dark);font-size:13.5px;display:flex;align-items:center;justify-content:center;text-transform:uppercase}
.social{position:absolute;top:165px;width:40px;height:40px;border-radius:50%;background:var(--white)}
.footer-rule{position:absolute;left:98px;top:271px;width:1004px;height:1px;background:rgba(255,255,255,.45)}
.copyright{position:absolute;left:98px;top:293px;font-size:13px}
.divider{position:absolute;top:44px;width:1px;height:190px;background:rgba(255,255,255,.15)}
</style>
</head>
<body>

<header class="site-header">
  <div class="brand"><span class="brand-mark"></span><span class="brand-name">caliber</span></div>
  <nav class="main-nav">
    <span class="active">Home</span><span>About Us</span><span>Services</span><span>Events</span><span>Our Partners</span><span>Contact Us</span>
    <svg width="16" height="16" viewBox="0 0 16 16"><circle cx="6.5" cy="6.5" r="5" fill="none" stroke="#0b8fd8" stroke-width="2"/><line x1="10.5" y1="10.5" x2="15" y2="15" stroke="#0b8fd8" stroke-width="2.4"/></svg>
  </nav>
</header>

<section class="hero">
  <div class="hero-photo" role="img" aria-label="Business person touching a glowing data dashboard with bar and line charts"></div>
  <h1 class="hero-title">Caliber Insight</h1>
  <p class="hero-sub">We provide services related to Big Data.</p>
  <div class="hero-btn">Learn More
    <svg width="10" height="16" viewBox="0 0 10 16"><polyline points="2,2 8,8 2,14" fill="none" stroke="#fff" stroke-width="2.2"/></svg>
  </div>
  <svg class="hero-arrow" style="left:36px" width="22" height="40" viewBox="0 0 22 40"><polyline points="18,2 4,20 18,38" fill="none" stroke="#fff" stroke-opacity=".7" stroke-width="2"/></svg>
  <svg class="hero-arrow" style="left:1132px" width="22" height="40" viewBox="0 0 22 40"><polyline points="4,2 18,20 4,38" fill="none" stroke="#fff" stroke-opacity=".7" stroke-width="2"/></svg>
</section>

<section class="welcome">
  <h2 class="section-title">Welcome to Caliber Insight</h2>
  <p>Lorem ipsum dolor sit amet, consectetur adipiscing elit, sed do eiusmod tempor incididunt ut labore et dolore magna aliqua. Ut enim ad minim veniam, quis nostrud exercitation ullamco laboris nisi ut aliquip ex ea commodo consequat. Duis aute irure dolor in reprehenderit in voluptate velit esse cillum dolore eu fugiat nulla pariatur.</p>
  <p>Sed ut perspiciatis unde omnis iste natus error sit voluptatem accusantium doloremque laudantium, totam rem aperiam, eaque ipsa quae ab illo inventore veritatis et quasi architecto beatae vitae dicta sunt explicabo.</p>
</section>

<section class="services">
  <h2 class="section-title">Our Services</h2>
  <p class="intro">At vero eos et accusamus et iusto odio dignissimos ducimus qui blanditiis praesentium voluptatum deleniti atque corrupti quos dolores et quas molestias excepturi sint occaecati cupiditate non provident.</p>
  <div class="service-list">
    <div class="service" style="left:77px">
      <svg width="124" height="108" viewBox="0 0 124 108"><polygon points="31,4 93,4 120,54 93,104 31,104 4,54" fill="#fff" stroke="#0b8fd8" stroke-width="8"/><rect x="44" y="62" width="8" height="12" fill="#0b8fd8"/><rect x="56" y="55" width="8" height="19" fill="#0b8fd8"/><rect x="68" y="48" width="8" height="26" fill="#0b8fd8"/><polyline points="42,54 58,42 68,46 82,32" fill="none" stroke="#0b8fd8" stroke-width="3"/></svg>
      <h3>Trends &amp; Predictions</h3>
      <p>Predictions for 2017: Innovation<br>Brings Digital Disruption</p>
      <span class="read-more">READ MORE</span>
    </div>
    <div class="service" style="left:287px">
      <svg width="124" height="108" viewBox="0 0 124 108"><polygon points="31,4 93,4 120,54 93,104 31,104 4,54" fill="#fff" stroke="#0b8fd8" stroke-width="8"/><rect x="40" y="36" width="40" height="28" fill="none" stroke="#0b8fd8" stroke-width="3"/><line x1="50" y1="70" x2="72" y2="70" stroke="#0b8fd8" stroke-width="3"/><circle cx="72" cy="54" r="8" fill="#fff" stroke="#0b8fd8" stroke-width="3"/><line x1="78" y1="60" x2="86" y2="68" stroke="#0b8fd8" stroke-width="3"/></svg>
      <h3>Data Analytics</h3>
      <p>Advance Your Business with<br>Advanced Analytics</p>
      <span class="read-more">READ MORE</span>
    </div>
    <div class="service" style="left:497px">
      <svg width="124" height="108" viewBox="0 0 124 108"><polygon points="31,4 93,4 120,54 93,104 31,104 4,54" fill="#fff" stroke="#0b8fd8" stroke-width="8"/><path d="M44 66 a10 10 0 0 1 2-20 a14 14 0 0 1 27-3 a11 11 0 0 1 6 23 z" fill="none" stroke="#0b8fd8" stroke-width="3"/><line x1="62" y1="48" x2="62" y2="72" stroke="#0b8fd8" stroke-width="3"/><polyline points="55,55 62,48 69,55" fill="none" stroke="#0b8fd8" stroke-width="3"/></svg>
      <h3>Cloud Computing</h3>
      <p>5 Ways Cloud Can Transform<br>Your Business</p>
      <span class="read-more">READ MORE</span>
    </div>
    <div class="service" style="left:707px">
      <svg width="124" height="108" viewBox="0 0 124 108"><polygon points="31,4 93,4 120,54 93,104 31,104 4,54" fill="#fff" stroke="#0b8fd8" stroke-width="8"/><circle cx="62" cy="54" r="9" fill="none" stroke="#0b8fd8" stroke-width="3"/><g fill="#0b8fd8"><circle cx="62" cy="34" r="4"/><circle cx="62" cy="74" r="4"/><circle cx="42" cy="54" r="4"/><circle cx="82" cy="54" r="4"/><circle cx="48" cy="40" r="3"/><circle cx="76" cy="40" r="3"/><circle cx="48" cy="68" r="3"/><circle cx="76" cy="68" r="3"/></g><g stroke="#0b8fd8" stroke-width="2"><line x1="62" y1="38" x2="62" y2="45"/><line x1="62" y1="63" x2="62" y2="70"/><line x1="46" y1="54" x2="53" y2="54"/><line x1="71" y1="54" x2="78" y2="54"/></g></svg>
      <h3>Internet of Things</h3>
      <p>Why IoT? Harness the Power of<br>Connected Things</p>
      <span class="read-more">READ MORE</span>
    </div>
    <div class="service" style="left:917px">
      <svg width="124" height="108" viewBox="0 0 124 108"><polygon points="31,4 93,4 120,54 93,104 31,104 4,54" fill="#fff" stroke="#0b8fd8" stroke-width="8"/><rect x="40" y="34" width="44" height="40" fill="none" stroke="#0b8fd8" stroke-width="3"/><circle cx="62" cy="49" r="7" fill="#0b8fd8"/><path d="M48 72 a14 12 0 0 1 28 0 z" fill="#0b8fd8"/></svg>
      <h3>Cio Leadership</h3>
      <p>Insights to Help CIOs Lead,<br>Transform, and Grow</p>
      <span class="read-more">READ MORE</span>
    </div>
  </div>
</section>

<section class="testimonials">
  <div class="testimonial-bg" role="img" aria-label="Blue tunnel of streaming binary data"></div>
  <h2 class="section-title">Client Testimonials</h2>
  <div class="quote">
    <span class="quote-mark" style="left:-44px;top:-8px">&ldquo;</span>
    But I must explain to you how all this mistaken idea of denouncing pleasure and praising pain was born and I will give you a complete account of the system, and expound the actual teachings of the great explorer of the truth, the master-builder of human happiness. No one rejects, dislikes, or avoids pleasure itself, because it is pleasure, but because those who do not know how to pursue pleasure rationally encounter consequences that are extremely painful
    <span class="quote-mark" style="right:-44px;bottom:-60px">&rdquo;</span>
  </div>
  <svg style="position:absolute;left:1082px;top:158px" width="18" height="36" viewBox="0 0 18 36"><polyline points="3,2 15,18 3,34" fill="none" stroke="#fff" stroke-opacity=".5" stroke-width="2"/></svg>
  <div class="avatar" role="img" aria-label="Portrait of client at a laptop"></div>
  <p class="client-name">Assumenda Est</p>
</section>

<section class="partners">
  <h2 class="section-title">Our Strategic Partners</h2>
  <svg class="partner-arrow" style="left:56px" width="18" height="34" viewBox="0 0 18 34"><polyline points="15,2 3,17 15,32" fill="none" stroke="#c8c8c8" stroke-width="3"/></svg>
  <div class="partner" style="left:98px">Harbourline</div>
  <div class="partner" style="left:268px">Orvane Group</div>
  <div class="partner" style="left:438px">Kestrel Bank</div>
  <div class="partner" style="left:608px">Lumora Networks</div>
  <div class="partner" style="left:778px">Fundwell</div>
  <div class="partner" style="left:948px">Ardenmoor</div>
  <svg class="partner-arrow" style="left:1128px" width="18" height="34" viewBox="0 0 18 34"><polyline points="3,2 15,17 3,32" fill="none" stroke="#c8c8c8" stroke-width="3"/></svg>
</section>

<footer class="site-footer">
  <h4 class="footer-head" style="left:98px">Quick Links</h4>
  <ul class="link-col" style="left:98px"><li>Home</li><li>About Us</li><li>Services</li><li>Events</li><li>Our Partners</li></ul>
  <ul class="link-col" style="left:279px"><li>Terms of Service</li><li>Privacy Policy</li><li>FAQ's</li></ul>
  <span class="divider" style="left:418px"></span>
  <h4 class="footer-head" style="left:461px">Contact Info</h4>
  <div class="contact">
    <div>Caliber Insight., Street Name,</div>
    <div>Address, Country, Pin Code.</div>
    <div class="contact-row"><svg width="14" height="14" viewBox="0 0 14 14"><path d="M3 1 l3 3 -2 2 a8 8 0 0 0 4 4 l2-2 3 3 -2 2 A11 11 0 0 1 1 3 z" fill="#fff"/></svg>(+01) 408-27153</div>
    <div class="contact-row"><svg width="14" height="12" viewBox="0 0 14 12"><rect x="0" y="1" width="14" height="10" fill="#fff"/><polyline points="0,1 7,7 14,1" fill="none" stroke="#0b8fd8" stroke-width="1.5"/></svg>hello@caliberinsight.com</div>
  </div>
  <span class="divider" style="left:738px"></span>
  <h4 class="footer-head" style="left:773px">Sign up for Newsletters</h4>
  <p class="newsletter-note">Please sign up here for latest news</p>
  <div class="signup"><span class="field">Email Address</span><span class="submit">Subscribe</span></div>
  <span class="social" style="left:775px"></span>
  <span class="social" style="left:823px"></span>
  <span class="social" style="left:872px"></span>
  <span class="social" style="left:920px"></span>
  <span class="footer-rule"></span>
  <p class="copyright">© 2017 CALIBER INSIGHT..  All right reserved . Term of Use</p>
</footer>

</body>
</html>
```